Verodex business card

Business card for sustainable investment company called "Verodex". Verodex is an exchange platform selling carbon credits between buyers and sellers. Carbon Credits are an environmental commodity for reducing global carbon emissions.

the card should obviously have our logo and the theme should be sustainability/environment mixed with a trading platform.

Contact Information for Business Card

Logo, Name, Title, Phone, Email

Colors
0054AA
0677BA
7BADD7
CADEEF
E8F1F8
0094D4
00A9DD
6FCCEA
C7EBF8
E9F6FB
00AB8E
00BBA5
67D7C9
C6EFE9
E9F9F6
59FF00
82FF00
B8FF75
E3FFCB
F4FFEA

```html
<!DOCTYPE html>
<html lang="en">
<head>
<meta charset="UTF-8">
<title>Verodex Business Card</title>
<link rel="stylesheet" href="https://fonts.googleapis.com/css2?family=Poppins:wght@400;500;600;700&display=swap">
<style>
  :root {
    --backdrop: #2b2b2d;
    --card-white: #ffffff;
    --ink-navy: #1a2b4a;
    --ink-body: #1f2533;
    --rule-grey: #9aa1ab;
    --brand-blue: #1f78f0;
    --grad-cyan: #2ee6ee;
    --grad-sky: #22b9ea;
    --grad-blue: #1f6ff0;
  }
  * { margin: 0; padding: 0; box-sizing: border-box; }
  html, body {
    width: 1200px;
    height: 1108px;
    overflow: hidden;
    background: var(--backdrop);
    font-family: "Poppins", sans-serif;
  }
  .card-set {
    position: absolute;
    inset: 0;
    display: flex;
    justify-content: center;
    align-items: center;
    gap: 80px;
  }
  .card {
    width: 380px;
    height: 650px;
    border-radius: 26px;
    position: relative;
    overflow: hidden;
    box-shadow: 0 18px 40px rgba(0,0,0,0.45);
  }
  .card-front {
    background: var(--card-white);
    display: flex;
    flex-direction: column;
    align-items: center;
  }
  .brand-lockup {
    margin-top: 170px;
    display: flex;
    align-items: center;
    gap: 16px;
  }
  .brand-square {
    width: 34px;
    height: 34px;
    background: var(--brand-blue);
    border-radius: 4px;
  }
  .brand-name {
    font-weight: 600;
    font-size: 46px;
    letter-spacing: 1px;
    color: var(--ink-navy);
    text-transform: uppercase;
    line-height: 1;
  }
  .person {
    margin-top: 210px;
    text-align: center;
  }
  .person-name {
    font-weight: 700;
    font-size: 27px;
    letter-spacing: 1px;
    color: var(--ink-navy);
    text-transform: uppercase;
    line-height: 1.1;
  }
  .person-title {
    font-weight: 400;
    font-size: 17px;
    letter-spacing: 0.5px;
    color: var(--ink-navy);
    text-transform: uppercase;
  }
  .contact-divider {
    margin-top: 20px;
    width: 300px;
    display: flex;
    align-items: center;
    gap: 8px;
  }
  .contact-divider .rule {
    flex: 1;
    height: 1px;
    background: var(--rule-grey);
  }
  .contact-icon {
    width: 28px;
    height: 28px;
    border-radius: 5px;
    background: var(--ink-navy);
    display: flex;
    align-items: center;
    justify-content: center;
  }
  .contact-list {
    margin-top: 12px;
    list-style: none;
    text-align: center;
    color: var(--ink-body);
    font-size: 18px;
    line-height: 1.4;
  }
  .card-back {
    background: linear-gradient(45deg, var(--grad-cyan) 0%, var(--grad-sky) 50%, var(--grad-blue) 100%);
  }
  .back-field {
    position: absolute;
    inset: 0;
  }
  .back-brand {
    position: absolute;
    right: 60px;
    bottom: 150px;
    display: flex;
    align-items: center;
    gap: 10px;
  }
  .back-brand .brand-square {
    width: 26px;
    height: 26px;
    background: var(--card-white);
  }
  .back-brand .brand-name {
    font-size: 26px;
    color: var(--card-white);
  }
</style>
</head>
<body>
  <main class="card-set">
    <section class="card card-front" aria-label="Card front">
      <div class="brand-lockup">
        <span class="brand-square" aria-hidden="true"></span>
        <span class="brand-name">Verodex</span>
      </div>

      <div class="person">
        <p class="person-name">Maren Holt</p>
        <p class="person-title">Managing Director</p>
      </div>

      <div class="contact-divider" aria-hidden="true">
        <span class="rule"></span>
        <span class="contact-icon">
          <svg width="16" height="16" viewBox="0 0 24 24" fill="#fff"><path d="M6.6 10.8a15.1 15.1 0 0 0 6.6 6.6l2.2-2.2c.3-.3.7-.4 1-.2 1.1.4 2.3.6 3.6.6.6 0 1 .4 1 1V20c0 .6-.4 1-1 1A17 17 0 0 1 3 4c0-.6.4-1 1-1h3.5c.6 0 1 .4 1 1 0 1.3.2 2.5.6 3.6.1.3 0 .7-.2 1z"/></svg>
        </span>
        <span class="contact-icon">
          <svg width="16" height="16" viewBox="0 0 24 24" fill="none" stroke="#fff" stroke-width="2"><rect x="3" y="5" width="18" height="14" rx="1"/><path d="M3 6l9 7 9-7"/></svg>
        </span>
        <span class="contact-icon">
          <svg width="16" height="16" viewBox="0 0 24 24" fill="none" stroke="#fff" stroke-width="2"><circle cx="12" cy="12" r="9"/><path d="M3 12h18M12 3c3 3.5 3 14.5 0 18M12 3c-3 3.5-3 14.5 0 18"/></svg>
        </span>
        <span class="rule"></span>
      </div>

      <ul class="contact-list">
        <li>044-555 210 480</li>
        <li>hello@verodex.com</li>
        <li>www.verodex.com</li>
      </ul>
    </section>

    <section class="card card-back" aria-label="Card back">
      <div class="back-field" role="img" aria-label="Faint embossed brand pattern across a cyan-to-blue gradient"></div>
      <div class="back-brand">
        <span class="brand-square" aria-hidden="true"></span>
        <span class="brand-name">Verodex</span>
      </div>
    </section>
  </main>
</body>
</html>
```